Need A Standard Musical Download Website

We are looking for a talented designer to create a unique web design for our startup Music website called Vorde Sound.
The website should be responsive and filled with some creative stuffs along with bright colors.

Vorde sound is a website loaded with different types of music and capable of downloading the requested music by its users.
There will be categories of music which would be sorted by the genre. They include RnB, Hip-Hop, Afro pop, Pop, Dancehall and Reggae).

DESIGN STYLE/THEME

Creative, trendy, colorful, unique, and easy to use. You have freedom of selecting which ever color suits you. The design must be energetic and attractive.

NAVIGATION

HOME-MUSIC(RnB, Hip hop, Afro pop, POP, dancehall, Reggae)-ARTISTE-NEWS-LOGIN

PAGES REQUIRED
------------
1)Home Page
2)Music

FONTS
GOOGLE FONTS is strongly recommended.

Designers can get inspiration from https://tunabrook.example

Industry/Entity Type

Startup

```html
<!DOCTYPE html>
<html lang="en">
<head>
<meta charset="utf-8">
<title>Vorde Sound — Enjoy Free Music</title>
<link href="https://fonts.googleapis.com/css2?family=Montserrat:wght@400;500;600;700;800&display=swap" rel="stylesheet">
<style>
:root{
  --black:#050508;
  --ink:#0c0b1c;
  --panel:rgba(10,9,26,.88);
  --orange:#f7941d;
  --red:#e8413f;
  --cyan:#2aa6d6;
  --white:#ffffff;
  --grey:#a9a7b8;
  --teal-btn:#0b5f86;
}
*{box-sizing:border-box;margin:0;padding:0}
html,body{width:994px;height:1200px;overflow:hidden;background:var(--black)}
body{font-family:'Montserrat',sans-serif;color:var(--white);position:relative}
.abs{position:absolute}

/* header */
.site-header{position:absolute;left:0;top:0;width:994px;height:54px;background:var(--black)}
.brand{position:absolute;display:flex;align-items:center;gap:6px;font-weight:700;color:var(--white)}
.brand-dot{width:10px;height:10px;border-radius:50%;background:var(--cyan)}
.site-header .brand{left:118px;top:14px;font-size:20px}
.main-nav{position:absolute;top:21px;left:453px;display:flex;gap:16px;font-size:8.5px;font-weight:700}
.main-nav a{color:var(--white);text-decoration:none}
.main-nav a.active{color:var(--orange)}
.search{position:absolute;left:660px;top:16px;width:150px;height:21px;border:1px solid #3a3a46;border-radius:11px;font-size:7.5px;color:#6d6c7a;padding:6px 10px;letter-spacing:.5px}
.search-btn{position:absolute;right:0;top:0;width:21px;height:19px;border-radius:0 10px 10px 0;background:#3a3a46}
.login-btn{position:absolute;left:817px;top:16px;width:57px;height:21px;border-radius:11px;background:var(--teal-btn);font-size:8.5px;font-weight:700;text-align:center;line-height:21px}

/* hero */
.hero{position:absolute;left:0;top:54px;width:994px;height:287px;background:linear-gradient(90deg,#1b1f6e 0%,#2b2f8a 45%,#4a3f8e 70%,#3a2e6a 100%)}
.hero-photo{position:absolute;right:0;top:0;width:420px;height:287px;background:radial-gradient(ellipse at 55% 40%,#8a7a9a 0%,#4a3e74 45%,rgba(43,47,138,0) 80%)}
.hero h1{position:absolute;left:117px;top:96px;font-size:37px;font-weight:700;letter-spacing:-1px;white-space:nowrap}
.hero p{position:absolute;left:118px;top:143px;width:312px;text-align:center;font-size:9.5px;line-height:11.5px;font-weight:500}
.cta{position:absolute;left:185px;top:176px;width:180px;height:24px;border-radius:12px;background:var(--orange);font-size:12.5px;font-weight:600;text-align:center;line-height:24px;color:#1a1233}
.slide-arrow{position:absolute;top:126px}

/* stage */
.stage{position:absolute;left:0;top:341px;width:994px;height:656px;background:linear-gradient(90deg,#3a0f55 0%,#24155e 50%,#15207a 100%)}
.player{position:absolute;left:119px;top:361px;width:755px;height:122px;background:var(--panel)}
.album-art{position:absolute;left:11px;top:20px;width:148px;height:83px;background:linear-gradient(135deg,#d9c3a5,#8a5a40 60%,#3a2a2a)}
.now{position:absolute;left:267px;top:23px;font-size:10px;font-weight:500;white-space:nowrap}
.now b{color:var(--orange);font-weight:500}
.controls{position:absolute;left:180px;top:48px;width:560px;height:20px}
.time{position:absolute;top:6px;font-size:8px}
.track{position:absolute;left:103px;top:9px;width:194px;height:2px;background:#3c3b52}
.track i{position:absolute;left:-3px;top:-3px;width:8px;height:8px;border-radius:50%;background:var(--white)}
.vol{position:absolute;left:493px;top:9px;width:62px;height:3px;background:#3c3b52}
.vol i{position:absolute;left:0;top:0;width:29px;height:3px;background:#d8d7e6}
.action{position:absolute;top:80px;display:flex;align-items:center;gap:6px;font-size:6px;font-weight:700;color:var(--red);line-height:6.5px}
.action span.ic{width:22px;height:22px;border-radius:50%;background:var(--red);display:flex;align-items:center;justify-content:center}

.genres{position:absolute;left:119px;top:496px;width:755px;height:34px;background:var(--panel);font-size:9.5px;font-weight:500;color:var(--grey)}
.genres span{position:absolute;top:12px}
.genres .on{color:var(--orange)}
.artist-select{position:absolute;left:571px;top:7px;width:150px;height:20px;border:1px solid #3a3a50;border-radius:10px;font-size:7.5px;color:#ccc;padding:5px 9px}
.artist-select i{position:absolute;right:0;top:0;width:21px;height:18px;border-radius:0 9px 9px 0;background:#3a3a46}

.library{position:absolute;left:119px;top:538px;width:755px;height:459px;background:var(--panel)}
.divider{position:absolute;left:378px;top:20px;width:1px;height:382px;background:#3a3152}
.col{position:absolute;top:25px}
.song{position:relative;height:49.6px;width:320px}
.thumb{position:absolute;left:0;top:7px;width:29px;height:29px;background:linear-gradient(135deg,#c9a98a,#6a3e30)}
.play{position:absolute;left:36px;top:8px}
.title{position:absolute;left:67px;top:12px;font-size:8px;font-weight:600;white-space:nowrap}
.title small{display:block;color:var(--orange);font-size:6.5px;font-weight:700;margin-top:3px}
.btns{position:absolute;left:227px;top:8px;display:flex;gap:5px}
.btns span{width:26px;height:26px;border-radius:50%;border:1.4px solid;display:flex;align-items:center;justify-content:center}
.b-heart{border-color:var(--red)!important}
.b-dl{border-color:var(--cyan)!important}
.b-share{border-color:var(--orange)!important}
.more{position:absolute;right:34px;top:426px;font-size:8px;font-weight:700;color:var(--orange)}

/* footer */
.site-footer{position:absolute;left:0;top:997px;width:994px;height:161px;background:linear-gradient(90deg,#4a1760 0%,#3a1a78 50%,#1d2a96 100%)}
.site-footer .brand{left:118px;top:45px;font-size:20px}
.socials{position:absolute;left:131px;top:81px;display:flex;gap:5px}
.socials i{width:15px;height:15px;border-radius:50%;background:#e04848;display:block}
.socials i:nth-child(1){background:#3b5bb0}.socials i:nth-child(2){background:#2aa6d6}.socials i:nth-child(5){background:#1a7bb5}
.foot-links{position:absolute;top:53px;list-style:none;font-size:8.5px;font-weight:700;line-height:16.6px}
.newsletter h4{position:absolute;left:701px;top:53px;font-size:8.5px;font-weight:700}
.email{position:absolute;left:701px;top:69px;width:173px;height:28px;background:var(--white);color:#333;font-size:8px;padding:10px 6px}
.submit{position:absolute;left:702px;top:105px;width:60px;height:22px;background:var(--teal-btn);font-size:9.5px;font-weight:700;text-align:center;line-height:22px;color:#cfe9f5}
.bottom-bar{position:absolute;left:0;top:1158px;width:994px;height:42px;background:var(--black);text-align:center;font-size:7.5px;font-weight:700;color:#8d8c99;line-height:42px}
</style>
</head>
<body>
<svg width="0" height="0" style="position:absolute">
  <defs>
    <symbol id="i-play" viewBox="0 0 26 26"><circle cx="13" cy="13" r="12" fill="none" stroke="#d9d8e4" stroke-width="1.4"/><path d="M10 7.5v11l8.5-5.5z" fill="#fff"/></symbol>
    <symbol id="i-heart" viewBox="0 0 12 12"><path d="M6 10.5 1.5 6A2.6 2.6 0 0 1 6 2.6 2.6 2.6 0 0 1 10.5 6z" fill="#e8413f"/></symbol>
    <symbol id="i-heart-w" viewBox="0 0 12 12"><path d="M6 10.5 1.5 6A2.6 2.6 0 0 1 6 2.6 2.6 2.6 0 0 1 10.5 6z" fill="#fff"/></symbol>
    <symbol id="i-dl" viewBox="0 0 12 12"><path d="M6 1.5v6M3.5 5 6 7.5 8.5 5M1.5 8v2h9V8" fill="none" stroke="#2aa6d6" stroke-width="1.2"/></symbol>
    <symbol id="i-dl-w" viewBox="0 0 12 12"><path d="M6 1.5v6M3.5 5 6 7.5 8.5 5M1.5 8v2h9V8" fill="none" stroke="#fff" stroke-width="1.3"/></symbol>
    <symbol id="i-share" viewBox="0 0 12 12"><path d="M9 2 3 6l6 4" fill="none" stroke="#f7941d" stroke-width="1.2"/><circle cx="9" cy="2" r="1.2" fill="#f7941d"/><circle cx="3" cy="6" r="1.2" fill="#f7941d"/><circle cx="9" cy="10" r="1.2" fill="#f7941d"/></symbol>
  </defs>
</svg>

<header class="site-header">
  <div class="brand"><span class="brand-dot"></span>Vorde Sound</div>
  <nav class="main-nav"><a class="active" href="#">HOME</a><a href="#">MUSIC</a><a href="#">ARTISTS</a><a href="#">NEWS</a></nav>
  <div class="search">SEARCH<span class="search-btn"></span></div>
  <div class="login-btn">LOGIN</div>
</header>

<section class="hero">
  <div class="hero-photo" role="img" aria-label="Photo of a guitarist performing with flowing hair"></div>
  <h1>Enjoy Free Music</h1>
  <p>Lorem ipsum dolor sit amet, consectetur adipiscing elit, sed do<br>eiusmod tempor incididunt ut labore et.</p>
  <div class="cta">30 free Songs with Trial</div>
  <svg class="slide-arrow" style="left:8px" width="18" height="34" viewBox="0 0 18 34"><path d="M16 2 3 17l13 15" fill="none" stroke="#b86a3a" stroke-width="3"/></svg>
  <svg class="slide-arrow" style="left:968px" width="18" height="34" viewBox="0 0 18 34"><path d="M2 2l13 15L2 32" fill="none" stroke="#b86a3a" stroke-width="3"/></svg>
</section>

<div class="stage"></div>

<section class="player">
  <div class="album-art" role="img" aria-label="Album cover for Rock &amp; Roll 2017 Reloaded"></div>
  <div class="now"><b>PLAYING NOW :</b> ROCK &amp; ROLL 2017 - RELOADED &nbsp;&nbsp;&nbsp;&nbsp;<b>ARTIST :</b> CAL MERROW</div>
  <div class="controls">
    <svg class="abs" style="left:0;top:4px" width="12" height="12" viewBox="0 0 12 12"><path d="M2 2v8M10 2 4 6l6 4z" stroke="#fff" fill="#fff"/></svg>
    <svg class="abs" style="left:21px;top:1px" width="16" height="18" viewBox="0 0 16 18"><path d="M2 1v16l13-8z" fill="#fff"/></svg>
    <svg class="abs" style="left:46px;top:4px" width="12" height="12" viewBox="0 0 12 12"><path d="M10 2v8M2 2l6 4-6 4z" stroke="#fff" fill="#fff"/></svg>
    <span class="time" style="left:75px">0:00</span>
    <div class="track"><i></i></div>
    <span class="time" style="left:336px">0:00</span>
    <svg class="abs" style="left:389px;top:3px" width="16" height="14" viewBox="0 0 16 14"><path d="M1 3h3l7 8h3M1 11h3l7-8h3M12 1l2 2-2 2M12 9l2 2-2 2" fill="none" stroke="#fff" stroke-width="1.5"/></svg>
    <svg class="abs" style="left:426px;top:3px" width="18" height="14" viewBox="0 0 18 14"><path d="M3 4h12v5H3zM12 1l3 3-3 3" fill="none" stroke="#fff" stroke-width="1.6"/></svg>
    <svg class="abs" style="left:463px;top:3px" width="18" height="14" viewBox="0 0 18 14"><path d="M1 5h3l5-4v12L4 9H1z" fill="#fff"/><path d="M11 4a4 4 0 0 1 0 6M13 2a7 7 0 0 1 0 10" fill="none" stroke="#fff" stroke-width="1.3"/></svg>
    <div class="vol"><i></i></div>
  </div>
  <div class="action" style="left:381px"><span class="ic"><svg width="12" height="12"><use href="#i-heart-w"/></svg></span>ADD TO<br>PLAYLIST</div>
  <div class="action" style="left:464px"><span class="ic"><svg width="12" height="12"><use href="#i-dl-w"/></svg></span>DOWNLOAD<br>NOW</div>
</section>

<nav class="genres">
  <span class="on" style="left:33px">RNB</span>
  <span style="left:79px">HIP-HOP</span>
  <span style="left:147px">AFRO POP</span>
  <span style="left:233px">POP</span>
  <span style="left:273px">DANCEHALL</span>
  <span style="left:368px">REGGAE</span>
  <span class="on" style="left:532px">ARTIST</span>
  <div class="artist-select">ALL<i></i></div>
</nav>

<section class="library">
  <div class="divider"></div>
  <div class="col" style="left:33px">
    <div class="song"><div class="thumb" role="img" aria-label="Album thumbnail"></div><svg class="play" width="26" height="26"><use href="#i-play"/></svg><div class="title">ROCK &amp; ROLL 2017 - RELOADED<small>CAL MERROW</small></div><div class="btns"><span class="b-heart"><svg width="11" height="11"><use href="#i-heart"/></svg></span><span class="b-dl"><svg width="11" height="11"><use href="#i-dl"/></svg></span><span class="b-share"><svg width="11" height="11"><use href="#i-share"/></svg></span></div></div>
    <div class="song"><div class="thumb" role="img" aria-label="Album thumbnail"></div><svg class="play" width="26" height="26"><use href="#i-play"/></svg><div class="title">ROCK &amp; ROLL 2017 - RELOADED<small>CAL MERROW</small></div><div class="btns"><span class="b-heart"><svg width="11" height="11"><use href="#i-heart"/></svg></span><span class="b-dl"><svg width="11" height="11"><use href="#i-dl"/></svg></span><span class="b-share"><svg width="11" height="11"><use href="#i-share"/></svg></span></div></div>
    <div class="song"><div class="thumb" role="img" aria-label="Album thumbnail"></div><svg class="play" width="26" height="26"><use href="#i-play"/></svg><div class="title">ROCK &amp; ROLL 2017 - RELOADED<small>CAL MERROW</small></div><div class="btns"><span class="b-heart"><svg width="11" height="11"><use href="#i-heart"/></svg></span><span class="b-dl"><svg width="11" height="11"><use href="#i-dl"/></svg></span><span class="b-share"><svg width="11" height="11"><use href="#i-share"/></svg></span></div></div>
    <div class="song"><div class="thumb" role="img" aria-label="Album thumbnail"></div><svg class="play" width="26" height="26"><use href="#i-play"/></svg><div class="title">ROCK &amp; ROLL 2017 - RELOADED<small>CAL MERROW</small></div><div class="btns"><span class="b-heart"><svg width="11" height="11"><use href="#i-heart"/></svg></span><span class="b-dl"><svg width="11" height="11"><use href="#i-dl"/></svg></span><span class="b-share"><svg width="11" height="11"><use href="#i-share"/></svg></span></div></div>
    <div class="song"><div class="thumb" role="img" aria-label="Album thumbnail"></div><svg class="play" width="26" height="26"><use href="#i-play"/></svg><div class="title">ROCK &amp; ROLL 2017 - RELOADED<small>CAL MERROW</small></div><div class="btns"><span class="b-heart"><svg width="11" height="11"><use href="#i-heart"/></svg></span><span class="b-dl"><svg width="11" height="11"><use href="#i-dl"/></svg></span><span class="b-share"><svg width="11" height="11"><use href="#i-share"/></svg></span></div></div>
    <div class="song"><div class="thumb" role="img" aria-label="Album thumbnail"></div><svg class="play" width="26" height="26"><use href="#i-play"/></svg><div class="title">ROCK &amp; ROLL 2017 - RELOADED<small>CAL MERROW</small></div><div class="btns"><span class="b-heart"><svg width="11" height="11"><use href="#i-heart"/></svg></span><span class="b-dl"><svg width="11" height="11"><use href="#i-dl"/></svg></span><span class="b-share"><svg width="11" height="11"><use href="#i-share"/></svg></span></div></div>
    <div class="song"><div class="thumb" role="img" aria-label="Album thumbnail"></div><svg class="play" width="26" height="26"><use href="#i-play"/></svg><div class="title">ROCK &amp; ROLL 2017 - RELOADED<small>CAL MERROW</small></div><div class="btns"><span class="b-heart"><svg width="11" height="11"><use href="#i-heart"/></svg></span><span class="b-dl"><svg width="11" height="11"><use href="#i-dl"/></svg></span><span class="b-share"><svg width="11" height="11"><use href="#i-share"/></svg></span></div></div>
    <div class="song"><div class="thumb" role="img" aria-label="Album thumbnail"></div><svg class="play" width="26" height="26"><use href="#i-play"/></svg><div class="title">ROCK &amp; ROLL 2017 - RELOADED<small>CAL MERROW</small></div><div class="btns"><span class="b-heart"><svg width="11" height="11"><use href="#i-heart"/></svg></span><span class="b-dl"><svg width="11" height="11"><use href="#i-dl"/></svg></span><span class="b-share"><svg width="11" height="11"><use href="#i-share"/></svg></span></div></div>
  </div>
  <div class="col" style="left:408px">
    <div class="song"><div class="thumb" role="img" aria-label="Album thumbnail"></div><svg class="play" width="26" height="26"><use href="#i-play"/></svg><div class="title">ROCK &amp; ROLL 2017 - RELOADED<small>CAL MERROW</small></div><div class="btns"><span class="b-heart"><svg width="11" height="11"><use href="#i-heart"/></svg></span><span class="b-dl"><svg width="11" height="11"><use href="#i-dl"/></svg></span><span class="b-share"><svg width="11" height="11"><use href="#i-share"/></svg></span></div></div>
    <div class="song"><div class="thumb" role="img" aria-label="Album thumbnail"></div><svg class="play" width="26" height="26"><use href="#i-play"/></svg><div class="title">ROCK &amp; ROLL 2017 - RELOADED<small>CAL MERROW</small></div><div class="btns"><span class="b-heart"><svg width="11" height="11"><use href="#i-heart"/></svg></span><span class="b-dl"><svg width="11" height="11"><use href="#i-dl"/></svg></span><span class="b-share"><svg width="11" height="11"><use href="#i-share"/></svg></span></div></div>
    <div class="song"><div class="thumb" role="img" aria-label="Album thumbnail"></div><svg class="play" width="26" height="26"><use href="#i-play"/></svg><div class="title">ROCK &amp; ROLL 2017 - RELOADED<small>CAL MERROW</small></div><div class="btns"><span class="b-heart"><svg width="11" height="11"><use href="#i-heart"/></svg></span><span class="b-dl"><svg width="11" height="11"><use href="#i-dl"/></svg></span><span class="b-share"><svg width="11" height="11"><use href="#i-share"/></svg></span></div></div>
    <div class="song"><div class="thumb" role="img" aria-label="Album thumbnail"></div><svg class="play" width="26" height="26"><use href="#i-play"/></svg><div class="title">ROCK &amp; ROLL 2017 - RELOADED<small>CAL MERROW</small></div><div class="btns"><span class="b-heart"><svg width="11" height="11"><use href="#i-heart"/></svg></span><span class="b-dl"><svg width="11" height="11"><use href="#i-dl"/></svg></span><span class="b-share"><svg width="11" height="11"><use href="#i-share"/></svg></span></div></div>
    <div class="song"><div class="thumb" role="img" aria-label="Album thumbnail"></div><svg class="play" width="26" height="26"><use href="#i-play"/></svg><div class="title">ROCK &amp; ROLL 2017 - RELOADED<small>CAL MERROW</small></div><div class="btns"><span class="b-heart"><svg width="11" height="11"><use href="#i-heart"/></svg></span><span class="b-dl"><svg width="11" height="11"><use href="#i-dl"/></svg></span><span class="b-share"><svg width="11" height="11"><use href="#i-share"/></svg></span></div></div>
    <div class="song"><div class="thumb" role="img" aria-label="Album thumbnail"></div><svg class="play" width="26" height="26"><use href="#i-play"/></svg><div class="title">ROCK &amp; ROLL 2017 - RELOADED<small>CAL MERROW</small></div><div class="btns"><span class="b-heart"><svg width="11" height="11"><use href="#i-heart"/></svg></span><span class="b-dl"><svg width="11" height="11"><use href="#i-dl"/></svg></span><span class="b-share"><svg width="11" height="11"><use href="#i-share"/></svg></span></div></div>
    <div class="song"><div class="thumb" role="img" aria-label="Album thumbnail"></div><svg class="play" width="26" height="26"><use href="#i-play"/></svg><div class="title">ROCK &amp; ROLL 2017 - RELOADED<small>CAL MERROW</small></div><div class="btns"><span class="b-heart"><svg width="11" height="11"><use href="#i-heart"/></svg></span><span class="b-dl"><svg width="11" height="11"><use href="#i-dl"/></svg></span><span class="b-share"><svg width="11" height="11"><use href="#i-share"/></svg></span></div></div>
    <div class="song"><div class="thumb" role="img" aria-label="Album thumbnail"></div><svg class="play" width="26" height="26"><use href="#i-play"/></svg><div class="title">ROCK &amp; ROLL 2017 - RELOADED<small>CAL MERROW</small></div><div class="btns"><span class="b-heart"><svg width="11" height="11"><use href="#i-heart"/></svg></span><span class="b-dl"><svg width="11" height="11"><use href="#i-dl"/></svg></span><span class="b-share"><svg width="11" height="11"><use href="#i-share"/></svg></span></div></div>
  </div>
  <div class="more">MORE MUSIC »</div>
</section>

<footer class="site-footer">
  <div class="brand"><span class="brand-dot"></span>Vorde Sound</div>
  <div class="socials"><i></i><i></i><i></i><i></i><i></i><i></i></div>
  <ul class="foot-links" style="left:373px"><li>HOME</li><li>MUSIC</li><li>ARTISTS</li><li>NEWS</li></ul>
  <ul class="foot-links" style="left:546px"><li>LOGIN</li><li>MY ACCOUNT</li><li>PRIVACY</li><li>CONTACT</li></ul>
  <div class="newsletter"><h4>NEWSLETTER SIGNUP</h4><div class="email">Email Address</div><div class="submit">SUBMIT</div></div>
</footer>
<div class="bottom-bar">© VORDE SOUND | ALL RIGHTS RESERVED</div>
</body>
</html>
```